Business Card Design

Velora Pixel Outreach

An online marketing consulting & strategy business for the cosmetic niche

We specialise in Increasing Leads, Conversions & Content Marketing

I am looking for a very clean, BOLD business card that is simple & effective

Target Market(s)

cosmetic surgeons & cosmetic clinics

Industry/Entity Type

Marketing

Contact Information for Business Card

Dermot Kalway
Online Marketing Strategist

Dermot@VeloraPixelOutreach.example
0492 158 620

LinkedIn: in/dermotkalway

```html
<!DOCTYPE html>
<html lang="en">
<head>
<meta charset="utf-8">
<title>Velora Pixel Outreach – Business Card</title>
<link rel="stylesheet" href="https://fonts.googleapis.com/css2?family=Michroma&family=Arimo:wght@400;700&display=swap">
<style>
  :root {
    --bg: #d4d4d4;
    --blue: #2fa6de;
    --green: #9fcb3a;
    --grey-text: #55585b;
    --ink: #3a3c3e;
    --white: #ffffff;
  }
  * { box-sizing: border-box; margin: 0; padding: 0; }
  html, body {
    width: 1200px; height: 985px; overflow: hidden;
    background: var(--bg);
    font-family: "Arimo", Arial, sans-serif;
  }
  .card {
    position: absolute; left: 240px;
    width: 720px; height: 412px;
    border-radius: 28px; overflow: hidden;
    box-shadow: 0 6px 18px rgba(0,0,0,.18);
  }
  /* Back side */
  .card--back {
    top: 50px;
    background: linear-gradient(30deg, var(--blue) 0%, #5bb8b0 40%, var(--green) 85%);
  }
  .card--back .brand {
    position: absolute; left: 200px; top: 165px;
    display: flex; align-items: center; gap: 22px;
  }
  .brand__dot {
    width: 74px; height: 74px; border-radius: 50%;
    background: var(--white); flex: none;
  }
  .brand__name {
    font-family: "Michroma", sans-serif;
    color: var(--white);
    font-size: 30px; line-height: 1.05;
    letter-spacing: 4px; text-transform: uppercase;
  }
  /* Front side */
  .card--front {
    top: 523px; background: var(--white);
  }
  .side-band {
    position: absolute; left: 0; top: 0; bottom: 0; width: 150px;
    background: linear-gradient(to top, var(--green) 0%, #6cbf8a 45%, var(--blue) 100%);
  }
  .rule {
    position: absolute; top: 0; bottom: 0; width: 3px;
  }
  .rule--green { left: 158px; background: var(--green); }
  .rule--blue  { left: 166px; background: var(--blue); }
  .logo-box {
    position: absolute; left: 36px; top: 34px;
    width: 150px; height: 112px; background: var(--white);
    display: flex; align-items: center; justify-content: center;
  }
  .logo-box .brand__dot {
    width: 78px; height: 78px; background: var(--blue);
  }
  .card--front .brand__name {
    position: absolute; left: 200px; top: 42px;
    color: var(--grey-text); font-size: 29px;
  }
  .person {
    position: absolute; left: 200px; top: 162px; width: 360px;
    border-bottom: 2px solid var(--green); padding-bottom: 6px;
  }
  .person__name { font-weight: 700; font-size: 27px; }
  .person__first { color: var(--blue); }
  .person__last { color: var(--green); }
  .person__role { color: var(--green); font-weight: 700; font-size: 18px; margin-top: 2px; }
  .contacts {
    position: absolute; left: 200px; top: 250px;
    list-style: none;
  }
  .contacts li {
    display: flex; align-items: center; gap: 14px;
    color: var(--ink); font-size: 19px; height: 40px;
  }
  .icon {
    width: 26px; height: 26px; background: var(--blue);
    border-radius: 3px; display: flex; align-items: center; justify-content: center; flex: none;
  }
</style>
</head>
<body>

<section class="card card--back">
  <div class="brand">
    <span class="brand__dot"></span>
    <div class="brand__name">Velora<br>Pixel<br>Outreach</div>
  </div>
</section>

<section class="card card--front">
  <div class="side-band"></div>
  <div class="rule rule--green"></div>
  <div class="rule rule--blue"></div>
  <div class="logo-box"><span class="brand__dot"></span></div>
  <div class="brand__name">Velora<br>Pixel<br>Outreach</div>

  <div class="person">
    <div class="person__name"><span class="person__first">Dermot</span> <span class="person__last">Kalway</span></div>
    <div class="person__role">Online Marketing Strategist</div>
  </div>

  <ul class="contacts">
    <li>
      <span class="icon">
        <svg width="16" height="16" viewBox="0 0 16 16"><path d="M4 1h3l1 4-2 1a8 8 0 0 0 4 4l1-2 4 1v3c0 1-1 2-2 2A13 13 0 0 1 2 3c0-1 1-2 2-2z" fill="#fff"/></svg>
      </span>
      0492 158 620
    </li>
    <li>
      <span class="icon">
        <svg width="18" height="14" viewBox="0 0 18 14"><rect x="1" y="1" width="16" height="12" fill="none" stroke="#fff" stroke-width="1.6"/><path d="M1 1l8 7 8-7" fill="none" stroke="#fff" stroke-width="1.6"/></svg>
      </span>
      Dermot@VeloraPixelOutreach.example
    </li>
    <li>
      <span class="icon"></span>
      in/dermotkalway
    </li>
  </ul>
</section>

</body>
</html>
```